KPL Construction we build lodges in Botswana

We need a Design Layout only with Categories where we can update each projects photos.... We have a web address and a host - kpl.construction

```html
<!DOCTYPE html>
<html lang="en">
<head>
<meta charset="utf-8">
<title>KPL Construction</title>
<link href="https://fonts.googleapis.com/css2?family=Poppins:wght@300;400;500;600;700&family=Open+Sans:wght@400;600&display=swap" rel="stylesheet">
<style>
:root{
  --green:#1e7b22;
  --green-dark:#16611a;
  --blue:#1f4e9c;
  --blue-dark:#173d7d;
  --orange:#f5821f;
  --ink:#1b1b1b;
  --text:#555;
  --light:#f2f2f2;
  --dark:#161616;
  --white:#fff;
}
*{margin:0;padding:0;box-sizing:border-box}
html,body{width:1200px;height:5085px;overflow:hidden}
body{position:relative;font-family:"Open Sans",sans-serif;color:var(--text);background:var(--white)}
.abs{position:absolute}
h1,h2,h3,h4{font-family:"Poppins",sans-serif;color:var(--ink)}

/* hero */
.hero{left:0;top:0;width:1200px;height:760px;background:linear-gradient(160deg,#3c4a2c 0%,#6b4a2b 35%,#8a5a32 55%,#3d3222 80%,#2a2a1e 100%)}
.hero-shade{left:0;top:0;width:1200px;height:760px;background:rgba(0,0,0,.35)}
.hero-curve{left:0;top:0}
.logo{left:140px;top:40px;display:flex;align-items:center;gap:12px;color:var(--white);font-family:"Poppins",sans-serif;font-weight:700;font-size:22px;letter-spacing:.5px}
.logo-mark{width:26px;height:26px;background:var(--white)}
.call{left:518px;top:48px;color:var(--white);font-family:"Poppins",sans-serif;font-size:20px;display:flex;align-items:center;gap:14px}
.call-icon{width:34px;height:34px;border:2px solid var(--white);border-radius:50%;display:flex;align-items:center;justify-content:center}
.search{left:790px;top:42px;width:262px;height:38px;background:var(--white);border-radius:19px;font-size:14px;color:#999;padding:9px 18px;display:flex;justify-content:space-between;align-items:center}
.nav{left:440px;top:104px;width:614px;display:flex;justify-content:space-between;font-family:"Poppins",sans-serif;font-weight:600;font-size:17px;color:var(--white)}
.hero-title{left:0;top:290px;width:1200px;text-align:center;color:var(--white);font-size:58px;font-weight:700;letter-spacing:1px}
.hero-sub{left:0;top:375px;width:1200px;text-align:center;color:var(--white);font-size:21px;line-height:31px}
.btn-ghost{display:inline-block;border:2px solid var(--white);border-radius:26px;color:var(--white);font-family:"Poppins",sans-serif;font-weight:600;font-size:16px;text-align:center}
.hero-btn{left:520px;top:450px;width:160px;height:50px;line-height:46px}
.arrow{width:30px;height:30px}

/* welcome */
.welcome{left:0;top:760px;width:1200px;height:477px;background:var(--light)}
.welcome-photo{left:205px;top:30px;width:290px;height:447px;background:linear-gradient(180deg,#d6d3cc 0%,#3b7a3a 45%,#2c6a2d 100%);border-radius:140px 140px 0 0}
.welcome-kicker{left:624px;top:70px;font-size:30px;font-weight:600}
.welcome-title{left:624px;top:110px;font-size:38px;font-weight:600}
.welcome-text{left:624px;top:180px;width:440px;font-size:14px;line-height:27px}
.btn-outline-green{left:624px;top:365px;width:138px;height:42px;line-height:38px;border:2px solid var(--green);border-radius:21px;color:var(--green);text-align:center;font-family:"Poppins",sans-serif;font-weight:600;font-size:14px}

.section-title{left:0;width:1200px;text-align:center;font-size:38px;font-weight:600;color:var(--ink)}

/* services */
.services{left:0;top:1447px;width:1200px;height:734px;display:grid;grid-template-columns:repeat(4,300px);grid-template-rows:repeat(2,367px)}
.photo{width:100%;height:100%}
.service-card{color:var(--white);text-align:center;padding:30px 26px 0;display:flex;flex-direction:column;align-items:center}
.service-card.blue{background:var(--blue)}
.service-card.green{background:var(--green)}
.service-card h3{color:var(--white);font-weight:400;font-size:25px;margin:20px 0 14px}
.service-card p{font-size:13px;line-height:22px}
.btn-small{margin-top:22px;border:2px solid var(--white);color:var(--white);font-family:"Poppins",sans-serif;font-size:14px;width:110px;height:36px;line-height:32px}

/* projects */
.projects{left:146px;top:2356px;width:908px;height:510px}
.proj{position:absolute}
.proj-card{background:var(--blue-dark);color:var(--white);text-align:center;padding:48px 30px 0}
.proj-card h3{color:var(--white);font-size:25px;font-weight:600;margin-bottom:10px}
.proj-card p{font-size:13px;line-height:22px}

/* newsletter */
.newsletter{left:0;top:3000px;width:1200px;height:322px;background:linear-gradient(180deg,#2856a8,#1f4c98)}
.newsletter h2{position:absolute;left:0;top:72px;width:1200px;text-align:center;color:var(--white);font-weight:300;font-size:33px;line-height:48px}
.field{position:absolute;top:200px;height:42px;background:var(--white);border-radius:21px;font-size:14px;color:#666;padding:11px 20px}
.subscribe{position:absolute;top:200px;left:793px;width:177px;height:42px;border-radius:21px;background:var(--orange);color:var(--white);font-family:"Poppins",sans-serif;font-weight:600;font-size:16px;text-align:center;line-height:42px}

/* testimonials */
.testimonials{left:0;top:3322px;width:1200px;height:526px;background:linear-gradient(180deg,#1e1e1a,#2b2a22 50%,#151513)}
.testimonials .section-title{color:var(--white);top:82px}
.quote-card{position:absolute;top:186px;width:410px;height:210px;background:var(--white);border-radius:6px;padding:30px 28px;font-size:13px;line-height:22px}
.quote-name{position:absolute;top:140px;font-size:14px;color:#333;line-height:22px}
.quote-mark{position:absolute;top:128px;font-family:"Poppins",sans-serif;font-size:60px;line-height:60px;color:#333}
.avatar{position:absolute;top:3633px;width:112px;height:112px;border-radius:50%;border:4px solid var(--white);background:linear-gradient(135deg,#b8a48c,#6b5a48)}

/* blog */
.blog{left:0;top:3848px;width:1200px;height:760px;background:radial-gradient(circle at 10% 20%,#eceff0 0 40px,transparent 41px),radial-gradient(circle at 85% 60%,#eceff0 0 30px,transparent 31px),#f7f8f8}
.blog-photo{left:153px;top:4034px;width:407px;height:311px;border:8px solid var(--white);box-shadow:0 4px 14px rgba(0,0,0,.2);background:linear-gradient(180deg,#8fb6cf 0%,#b49a6b 45%,#6d5a3a 70%,#4f6b34 100%)}
.blog-title{left:610px;top:4050px;width:460px;font-size:29px;font-weight:600;line-height:40px;text-transform:uppercase}
.blog-meta{left:610px;top:4140px;font-size:14px;color:#666;display:flex;gap:30px}
.blog-text{left:610px;top:4178px;width:460px;font-size:13px;line-height:25px}
.blog-btn{left:610px;top:4315px;width:112px;height:34px;border:2px solid #333;border-radius:17px;text-align:center;line-height:30px;font-family:"Poppins",sans-serif;font-weight:600;font-size:12px;color:#333}

/* footer */
.footer{left:0;top:4600px;width:1200px;height:315px;background:var(--dark);color:#ddd}
.footer h4{color:var(--white);font-size:17px;font-weight:600;position:absolute;top:28px}
.footer ul{list-style:none;position:absolute;top:70px;font-size:14px;line-height:27px}
.footer li{display:flex;align-items:center;gap:10px}
.dot{width:22px;height:22px;border:1.5px solid #bbb;border-radius:50%;flex:none}
.email-field{position:absolute;left:478px;top:125px;width:275px;height:34px;background:var(--white);border-radius:17px;font-size:12px;color:#777;padding:8px 16px}
.btn-sub{position:absolute;left:478px;top:175px;width:105px;height:32px;background:var(--green);border-radius:16px;color:var(--white);text-align:center;line-height:32px;font-size:13px;font-weight:600}
.copyright{left:0;top:4915px;width:1200px;height:170px;background:#0d0d0d;border-top:1px solid #2a2a2a}
.copyright p{position:absolute;top:46px;width:1200px;text-align:center;color:#ddd;font-size:16px}
.copy-icons{position:absolute;top:88px;left:541px;display:flex;gap:10px}
.copy-icons span{width:28px;height:28px;border:1.5px solid #ccc;border-radius:50%}
</style>
</head>
<body>

<!-- Hero -->
<div class="abs hero" role="img" aria-label="Timber lodge with wooden balconies among trees"></div>
<div class="abs hero-shade"></div>
<svg class="abs hero-curve" width="1200" height="760" viewBox="0 0 1200 760">
  <path d="M0 600 L600 745 L1200 600 V760 H0 Z" fill="#1e7b22"/>
  <path d="M0 618 L600 752 L1200 618 V760 H0 Z" fill="#f2f2f2"/>
</svg>
<div class="abs logo"><span class="logo-mark"></span>KPL CONSTRUCTION</div>
<div class="abs call">Call (555) 014-2300
  <span class="call-icon"><svg width="16" height="16" viewBox="0 0 24 24"><path d="M6.6 10.8a15 15 0 0 0 6.6 6.6l2.2-2.2c.3-.3.7-.4 1-.2 1.1.4 2.3.6 3.6.6.6 0 1 .4 1 1V20c0 .6-.4 1-1 1A17 17 0 0 1 3 4c0-.6.4-1 1-1h3.5c.6 0 1 .4 1 1 0 1.3.2 2.5.6 3.6.1.3 0 .7-.2 1z" fill="#fff"/></svg></span>
</div>
<div class="abs search"><span>Search</span><svg width="14" height="14" viewBox="0 0 24 24"><circle cx="10" cy="10" r="7" fill="none" stroke="#333" stroke-width="2.5"/><path d="M15 15l6 6" stroke="#333" stroke-width="2.5"/></svg></div>
<nav class="abs nav"><span>HOME</span><span>ABOUT US</span><span>OUR SERVICES</span><span>PROJECTS</span><span>BLOG</span><span>CONTACT</span></nav>
<h1 class="abs hero-title">KPL CONSTRUCTION</h1>
<p class="abs hero-sub">Sed ut perspiciatis unde omnis iste natus<br>voluptatem accusantium doloremque laudantium.</p>
<a class="abs btn-ghost hero-btn">LEARN MORE</a>
<svg class="abs arrow" style="left:110px;top:348px" viewBox="0 0 30 30"><path d="M19 6 L10 15 L19 24" fill="none" stroke="#fff" stroke-width="3"/></svg>
<svg class="abs arrow" style="left:1060px;top:348px" viewBox="0 0 30 30"><path d="M11 6 L20 15 L11 24" fill="none" stroke="#fff" stroke-width="3"/></svg>

<!-- Welcome -->
<section class="abs welcome">
  <svg class="abs" style="left:130px;top:140px" width="260" height="260" viewBox="0 0 260 260">
    <circle cx="60" cy="70" r="55" fill="#cfe3c5"/>
    <circle cx="140" cy="150" r="100" fill="#f7e8b0"/>
  </svg>
  <div class="abs welcome-photo" role="img" aria-label="Smiling builder in hard hat and green shirt with crossed arms"></div>
  <h2 class="abs welcome-kicker">WELCOME TO</h2>
  <h2 class="abs welcome-title">KPL CONSTRUCTION</h2>
  <p class="abs welcome-text">Sed ut perspiciatis unde omnis iste natus error sit voluptatem accusantium doloremque laudantium, totam rem aperiam, eaque ipsa quae ab illo inventore veritatis et quasi architecto beatae vitae dicta sunt explicabo. Nemo enim ipsam voluptatem quia voluptas sit aspernatur aut odit aut fugit, sed quia consequuntur magni d</p>
  <a class="abs btn-outline-green">READ MORE</a>
</section>

<!-- Services -->
<h2 class="abs section-title" style="top:1312px">OUR SERVICES</h2>
<section class="abs services">
  <div class="photo" role="img" aria-label="Builders reviewing plans with clients" style="background:linear-gradient(135deg,#e2c24a,#8a6a48 50%,#3a4a6a)"></div>
  <div class="service-card blue">
    <svg width="56" height="56" viewBox="0 0 56 56" fill="none" stroke="#fff" stroke-width="2.5"><path d="M10 46 L36 20"/><path d="M32 12 a8 8 0 0 0 12 12 l-4-4 z"/><path d="M12 12 L44 44"/><rect x="8" y="8" width="10" height="10"/></svg>
    <h3>Construction</h3>
    <p>Sed ut perspiciatis unde omnis iste natus error sit voluptatem accusantium doloremque laudantium, totam rem aperiam, eaque ipsa quae.</p>
    <span class="btn-small">Read More</span>
  </div>
  <div class="photo" role="img" aria-label="Agent handing house keys to a couple" style="background:linear-gradient(135deg,#e9e5dc,#6b6a70 50%,#2e2e36)"></div>
  <div class="service-card green">
    <svg width="56" height="56" viewBox="0 0 56 56" fill="none" stroke="#fff" stroke-width="2.5"><path d="M8 28 L28 10 L48 28"/><path d="M14 24 V46 H42 V24"/><rect x="24" y="32" width="8" height="14"/></svg>
    <h3>Quality Home Builders</h3>
    <p>Sed ut perspiciatis unde omnis iste natus error sit voluptatem accusantium doloremque laudantium, totam rem aperiam, eaque ipsa quae.</p>
    <span class="btn-small">Read More</span>
  </div>
  <div class="service-card green">
    <svg width="56" height="56" viewBox="0 0 56 56" fill="none" stroke="#fff" stroke-width="2.5"><rect x="12" y="8" width="32" height="40"/><path d="M18 18 H38 M18 26 H38 M18 34 H30"/></svg>
    <h3>Planning</h3>
    <p>Sed ut perspiciatis unde omnis iste natus error sit voluptatem accusantium doloremque laudantium, totam rem aperiam, eaque ipsa quae.</p>
    <span class="btn-small">Read More</span>
  </div>
  <div class="photo" role="img" aria-label="Engineer in hard hat drawing plans at a desk" style="background:linear-gradient(135deg,#d9d4c8,#b8a05a 50%,#4e4a44)"></div>
  <div class="service-card blue">
    <svg width="56" height="56" viewBox="0 0 56 56" fill="none" stroke="#fff" stroke-width="2.5"><circle cx="28" cy="12" r="4"/><path d="M26 16 L14 48 M30 16 L42 48 M18 38 H38"/></svg>
    <h3>Development</h3>
    <p>Sed ut perspiciatis unde omnis iste natus error sit voluptatem accusantium doloremque laudantium, totam rem aperiam, eaque ipsa quae.</p>
    <span class="btn-small">Read More</span>
  </div>
  <div class="photo" role="img" aria-label="Two-storey family house with lawn" style="background:linear-gradient(180deg,#9bc2e4 0%,#c9c2a6 45%,#6a8a44 75%,#3f7a2a 100%)"></div>
</section>

<!-- Projects -->
<h2 class="abs section-title" style="top:2258px">OUR PROJECTS</h2>
<section class="abs projects">
  <div class="proj" role="img" aria-label="Lodge bedroom with timber walls" style="left:0;top:0;width:454px;height:255px;background:linear-gradient(135deg,#c27a3e,#7a3e1e 60%,#3e1e10)"></div>
  <div class="proj" role="img" aria-label="Guest on a wooden lodge deck" style="left:454px;top:0;width:454px;height:255px;background:linear-gradient(180deg,#9fc4e0,#6a5238 55%,#3a2a1c)"></div>
  <div class="proj" role="img" aria-label="Thatched lodge over a lake with hills" style="left:0;top:255px;width:304px;height:255px;background:linear-gradient(180deg,#a9c8e6 0%,#7a9a6a 45%,#4a6a8a 70%,#2e4a6a 100%)"></div>
  <div class="proj" role="img" aria-label="Timber lodge walkway among trees" style="left:304px;top:255px;width:310px;height:255px;background:linear-gradient(135deg,#5a7a3a,#7a4a24 55%,#2a1e12)"></div>
  <div class="proj proj-card" style="left:614px;top:255px;width:294px;height:255px">
    <h3>CONSTRUCTION</h3>
    <p>Sed ut perspiciatis unde omnis iste natus error sit voluptatem accusantium doloremque laudantium.</p>
    <span class="btn-small" style="display:inline-block">READ MORE</span>
  </div>
</section>

<!-- Newsletter -->
<section class="abs newsletter">
  <h2>Download Our Project Brochure To View<br>Our Shared Housing Developments In Detail</h2>
  <div class="field" style="left:227px;width:271px">Your First Name</div>
  <div class="field" style="left:512px;width:268px">Your email</div>
  <div class="subscribe">SUBSCRIBE</div>
</section>

<!-- Testimonials -->
<section class="abs testimonials">
  <h2 class="abs section-title">WHAT OUR CLIENTS SAY</h2>
  <div class="quote-card" style="left:153px">
    Sed ut perspiciatis unde omnis iste natus error sit voluptatem accusantium doloremque laudantium, totam rem aperiam, eaque ipsa quae ab illo inventore veritatis et quasi architecto beatae vitae dicta sunt explicabo.
    <div class="quote-name" style="left:28px">John Doe -<br>KPL Construction</div>
    <div class="quote-mark" style="left:230px">&rdquo;</div>
  </div>
  <div class="quote-card" style="left:634px">
    Sed ut perspiciatis unde omnis iste natus error sit voluptatem accusantium doloremque laudantium, totam rem aperiam, eaque ipsa quae ab illo inventore veritatis et quasi architecto beatae vitae dicta sunt explicabo.
    <div class="quote-name" style="right:28px;text-align:right">John Doe -<br>KPL Construction</div>
    <div class="quote-mark" style="left:140px">&ldquo;</div>
  </div>
</section>
<div class="avatar" role="img" aria-label="Client portrait" style="left:459px"></div>
<div class="avatar" role="img" aria-label="Client portrait" style="left:605px"></div>

<!-- Blog -->
<section class="abs blog"></section>
<h2 class="abs section-title" style="top:3912px">LATEST BLOG</h2>
<div class="abs blog-photo" role="img" aria-label="Thatched lodge with outdoor seating"></div>
<h3 class="abs blog-title">Quis autem vel eum iure reprehenderit qui in</h3>
<div class="abs blog-meta"><span>&#9635; March 25, 2019</span><span>&#9675; 2 comments</span></div>
<p class="abs blog-text">Sed ut perspiciatis unde omnis iste natus error sit voluptatem accusantium doloremque laudantium, totam rem aperiam, eaque ipsa quae ab illo inventore veritatis et quasi architecto beatae vitae dicta sunt explicabo. Nemo enim ipsam voluptatem quia voluptas sit aspernatur</p>
<a class="abs blog-btn">LEARN MORE</a>
<svg class="abs arrow" style="left:55px;top:4165px" viewBox="0 0 30 30"><path d="M19 4 L9 15 L19 26" fill="none" stroke="#999" stroke-width="2"/></svg>
<svg class="abs arrow" style="left:1120px;top:4165px" viewBox="0 0 30 30"><path d="M11 4 L21 15 L11 26" fill="none" stroke="#999" stroke-width="2"/></svg>

<!-- Footer -->
<svg class="abs" style="left:0;top:4455px" width="1200" height="150" viewBox="0 0 1200 150">
  <path d="M0 145 L600 5 L1200 145 V150 H0 Z" fill="#1e7b22"/>
  <path d="M0 150 L600 25 L1200 150 Z" fill="#161616"/>
</svg>
<footer class="abs footer">
  <h4 style="left:142px">CONTACT US</h4>
  <ul style="left:142px;width:300px">
    <li><svg width="14" height="18" viewBox="0 0 14 18"><path d="M7 1a6 6 0 0 1 6 6c0 4-6 10-6 10S1 11 1 7a6 6 0 0 1 6-6z" fill="none" stroke="#ddd" stroke-width="1.5"/><circle cx="7" cy="7" r="2" fill="#ddd"/></svg><span>KPL Construction<br>118 Kgale View Rd,<br>Gaborone, BW 00267</span></li>
    <li style="margin-top:8px"><svg width="14" height="14" viewBox="0 0 24 24"><path d="M6.6 10.8a15 15 0 0 0 6.6 6.6l2.2-2.2c.3-.3.7-.4 1-.2 1.1.4 2.3.6 3.6.6.6 0 1 .4 1 1V20c0 .6-.4 1-1 1A17 17 0 0 1 3 4c0-.6.4-1 1-1h3.5c.6 0 1 .4 1 1 0 1.3.2 2.5.6 3.6.1.3 0 .7-.2 1z" fill="#ddd"/></svg>Phone: (555) 014-2300</li>
    <li><svg width="14" height="12" viewBox="0 0 14 12"><rect x="1" y="1" width="12" height="10" fill="none" stroke="#ddd" stroke-width="1.5"/><path d="M1 1 L7 6 L13 1" fill="none" stroke="#ddd" stroke-width="1.5"/></svg>Email: info@kpl.construction</li>
  </ul>
  <h4 style="left:478px">SIGN UP TO RECEIVE EMAIL</h4>
  <p style="position:absolute;left:478px;top:70px;width:280px;font-size:13px;line-height:21px">Excepteur sint occaecat cupidatat non proident, sunt in culpa qui fenda</p>
  <div class="email-field">Enter Email</div>
  <div class="btn-sub">SUBSCRIBE</div>
  <h4 style="left:803px">QUICK LINKS</h4>
  <ul style="left:803px;line-height:26px"><li>Home</li><li>Company</li><li>Services</li><li>Projects</li><li>Blog</li><li>Contact</li></ul>
  <h4 style="left:966px">SOCIAL</h4>
  <ul style="left:966px;line-height:32px"><li><span class="dot"></span>Friendbook</li><li><span class="dot"></span>Chirper</li><li><span class="dot"></span>Circles</li><li><span class="dot"></span>Viewtube</li></ul>
</footer>
<div class="abs copyright">
  <p>Copyright &copy; KPL Construction. 2019. All rights reserved.</p>
  <div class="copy-icons"><span></span><span></span><span></span><span></span></div>
</div>

</body>
</html>
```